Web Site Design and Business Card design for Recruiting Company

There are three major tasks in this project:
1) I need to re-design my newly created website www.talvoro.net using the same logo but creating a totally different recruiting template that will apply better for a recruitment site. I want to use the elements of the Talvoro Network logo (which is the road junction) and red, black and gray colors throughout the website. I need someone to both design and launch the site...
2) I would also like to design a double sided business card using the same logo/colors and elements as described above
3) I would also like to have a small thumbnail logo created. As our large logo cannot be previewed easily on the Pelmwork or on Google Chrome tab images

The design should be contemporary, minimalist and slick

```html
<!DOCTYPE html>
<html lang="en">
<head>
<meta charset="utf-8">
<title>Talvoro Network – Recruiting</title>
<link href="https://fonts.googleapis.com/css2?family=Lato:wght@400;700&family=Varela+Round&display=swap" rel="stylesheet">
<style>
:root{
  --red:#d7101f;
  --black:#151515;
  --ink:#222;
  --muted:#666;
  --gray-bg:#f3f3f5;
  --wave:#dde1e6;
  --line:#bdbdbd;
}
*{box-sizing:border-box;margin:0;padding:0}
html,body{width:1200px;height:3045px;overflow:hidden}
body{position:relative;background:#fff;font-family:'Lato',sans-serif;color:var(--ink)}
.abs{position:absolute}
.head-font{font-family:'Varela Round',sans-serif;font-weight:400}
.red{color:var(--red)}

/* header */
.brand{left:154px;top:44px;display:flex;align-items:center;gap:10px;font-size:22px;color:var(--black);font-weight:700}
.brand-dot{width:22px;height:22px;border-radius:50%;background:var(--red)}
.nav{top:58px;left:0;width:1200px;font-size:14px}
.nav a{position:absolute;color:var(--ink);text-decoration:none;letter-spacing:.2px}
.nav a.active{color:var(--red)}
.nav a.active::after{content:"";position:absolute;left:0;right:0;bottom:-10px;height:2px;background:var(--red)}
.top-search{left:813px;top:51px;width:247px;height:34px;border-radius:17px;box-shadow:0 2px 8px rgba(0,0,0,.12);background:#fff;font-size:12px;color:var(--muted);padding:10px 16px}
.top-search .go{position:absolute;right:8px;top:7px;width:20px;height:20px;border-radius:50%;background:var(--red)}

/* hero */
.hero-title{left:141px;top:205px;font-size:71px;line-height:63px;color:var(--black)}
.hero-sub{left:143px;top:355px;font-size:16px;color:#444}
.hero-search{left:144px;top:410px;width:383px;height:39px;display:flex}
.hero-search .field{flex:1;border:1px solid #ccc;font-size:12px;color:#555;padding:12px 16px}
.hero-search .btn{width:110px;background:var(--red);color:#fff;font-weight:700;font-size:16px;display:flex;align-items:center;justify-content:center}
.hero-art{left:597px;top:160px;width:461px;height:348px;border-radius:60px 90px 70px 120px;background:linear-gradient(160deg,#fbe3e6,#f3c6cc 70%,#fff 100%)}

/* welcome */
.welcome{left:0;top:612px;width:1200px;text-align:center}
.welcome h2{font-size:40px;line-height:46px;color:var(--black)}
.welcome p{width:660px;margin:26px auto 0;font-size:14.5px;line-height:32px;color:#444}
.pill{position:absolute;height:46px;border-radius:23px;color:#fff;font-weight:700;font-size:16px;display:flex;align-items:center;justify-content:center;gap:8px}
.pill.red-bg{background:var(--red)}
.pill.dark{background:var(--black)}
.arrow-dot{width:14px;height:14px;border-radius:50%;background:#fff;position:relative}
.arrow-dot::after{content:"";position:absolute;left:4px;top:4px;border-left:6px solid currentColor;border-top:3px solid transparent;border-bottom:3px solid transparent}
.red-bg .arrow-dot::after{border-left-color:var(--red)}
.dark .arrow-dot::after{border-left-color:var(--black)}

/* grey bands */
.band{left:0;width:1200px;background:var(--gray-bg)}
.section-title{left:0;width:1200px;text-align:center;font-size:42px;color:var(--black)}

/* job cards */
.job{width:438px;height:173px;background:#fff;box-shadow:0 2px 10px rgba(0,0,0,.1);border-radius:3px}
.job .tag{position:absolute;left:0;top:0;width:26px;height:26px;background:var(--red);border-radius:0 0 14px 0;color:#fff;font-size:12px;text-align:center;line-height:24px}
.job h3{position:absolute;left:28px;top:33px;font-size:20px;font-weight:700;color:var(--black)}
.job .heart{position:absolute;right:12px;top:30px;width:32px;height:32px;border:1.5px solid #bbb;border-radius:50%;color:#999;font-size:14px;text-align:center;line-height:30px}
.job ul{position:absolute;left:28px;top:76px;list-style:none;font-size:11.5px;color:#555}
.job li{height:28.5px;display:flex;align-items:flex-start;gap:10px}
.job li i{width:10px;height:10px;display:inline-block;background:#888;border-radius:50%;margin-top:2px}
.job .hire{position:absolute;right:14px;top:106px;width:96px;height:35px;border-radius:18px;background:var(--black);color:#fff;font-size:11px;font-weight:700;text-align:center;line-height:35px}

/* services */
.service{width:300px;text-align:center}
.service .ring-wrap{position:relative;height:160px}
.service .bg{position:absolute;left:30px;top:0;width:242px;height:158px;background:linear-gradient(90deg,#e9e9e9,#fafafa 50%,#e9e9e9)}
.service .ring{position:absolute;left:79px;top:8px;width:142px;height:142px;border-radius:50%;border:8px solid var(--red);background:#fff;display:flex;align-items:center;justify-content:center}
.service h3{margin-top:12px;font-size:25px;line-height:28px;color:var(--black)}
.down{display:inline-block;margin-top:10px;width:20px;height:20px;border-radius:50%;background:var(--red);position:relative}
.down::after{content:"";position:absolute;left:5px;top:7px;border-top:7px solid #fff;border-left:5px solid transparent;border-right:5px solid transparent}

/* contact */
.input{height:45px;border:1.5px solid #999;background:#fff;font-size:14px;color:#444;padding:13px 20px}
.input.msg{height:84px}

/* footer */
.footer{left:0;top:2880px;width:1200px;height:165px;background:var(--black);color:#fff;text-align:center}
.social{position:absolute;width:40px;height:40px;border:1.5px solid #fff;border-radius:50%;top:29px}
.social::after{content:"";position:absolute;left:13px;top:13px;width:12px;height:12px;border-radius:50%;background:var(--red)}
.footer .info{position:absolute;top:84px;width:1200px;font-size:14px}
.footer .copy{position:absolute;top:118px;width:1200px;font-size:13px}
</style>
</head>
<body>

<!-- header -->
<div class="abs brand"><span class="brand-dot"></span>Talvoro Network</div>
<nav class="abs nav">
  <a class="active" style="left:425px">HOME</a>
  <a style="left:498px">ABOUT US</a>
  <a style="left:596px">SERVICES</a>
  <a style="left:689px">CONTACT US</a>
</nav>
<div class="abs top-search">Search..<span class="go"></span></div>

<!-- hero -->
<h1 class="abs hero-title head-font">Talvoro<br>Network</h1>
<p class="abs hero-sub">Lorem ipsum dolor sit amet consectetur adipiscing elit</p>
<div class="abs hero-search"><div class="field">Search Jobs</div><div class="btn">SERACH</div></div>
<div class="abs hero-art" role="img" aria-label="Illustration of two business people shaking hands beside a reception desk"></div>

<!-- welcome -->
<section class="abs welcome">
  <h2 class="head-font">Welcome to<br>Talvoro Network</h2>
  <p>Talvoro Network LLC is an Atlanta based talent advisory, recruiting and staffing firm. We help companies find skilled professionals within the shortest time frames though our unique network of business and personal connections nationwide and overseas.</p>
</section>
<div class="pill red-bg" style="left:365px;top:856px;width:230px">REGISTER WITH US <span class="arrow-dot"></span></div>
<div class="pill dark" style="left:605px;top:856px;width:230px">CREATE JOB ALERT <span class="arrow-dot"></span></div>

<!-- recent jobs -->
<div class="abs band" style="top:1060px;height:678px"></div>
<svg class="abs" style="left:0;top:995px" width="1200" height="90" viewBox="0 0 1200 90">
  <path d="M0 45 C200 0 450 10 600 15 C800 10 1000 0 1200 30 L1200 90 L0 90Z" fill="#f3f3f5"/>
  <path d="M30 45 C150 20 300 20 530 52 C380 80 200 90 30 45Z" fill="#e4e7eb"/>
  <path d="M90 60 C200 45 320 45 430 70 C320 90 180 88 90 60Z" fill="#cfd5dc"/>
  <path d="M1065 45 C1120 30 1170 25 1200 25 L1200 80 C1150 70 1100 60 1065 45Z" fill="#dfe3e8"/>
</svg>
<h2 class="abs section-title head-font" style="top:1110px">Recent <span class="red">Jobs</span></h2>

<div class="abs job" style="left:145px;top:1195px"><span class="tag">★</span><h3>Project Management</h3><span class="heart">♥</span>
<ul><li><i></i>JOB TITLE - Project</li><li><i></i>LOCATION - Sydney</li><li><i></i>JOB TYPE - Contractor</li></ul><span class="hire">HIRE NOW</span></div>
<div class="abs job" style="left:617px;top:1195px"><span class="tag">★</span><h3>Construction Management</h3><span class="heart">♥</span>
<ul><li><i></i>JOB TITLE - Construction</li><li><i></i>LOCATION - Sydney</li><li><i></i>JOB TYPE - Contractor</li></ul><span class="hire">HIRE NOW</span></div>
<div class="abs job" style="left:145px;top:1396px"><span class="tag">★</span><h3>Network Optimization</h3><span class="heart">♥</span>
<ul><li><i></i>JOB TITLE - Network Optimization</li><li><i></i>LOCATION - Sydney</li><li><i></i>JOB TYPE - Contractor</li></ul><span class="hire">HIRE NOW</span></div>
<div class="abs job" style="left:617px;top:1396px"><span class="tag">★</span><h3>Quality Assurance</h3><span class="heart">♥</span>
<ul><li><i></i>JOB TITLE - QA</li><li><i></i>LOCATION - Sydney</li><li><i></i>JOB TYPE - Contractor</li></ul><span class="hire">HIRE NOW</span></div>

<div class="pill red-bg" style="left:485px;top:1611px;width:229px">VIEW MORE JOBS <span class="arrow-dot"></span></div>

<!-- services -->
<h2 class="abs section-title head-font" style="top:1810px">Our <span class="red">Services</span></h2>

<div class="abs service" style="left:116px;top:1917px">
  <div class="ring-wrap"><div class="bg" role="img" aria-label="Faint crossing line pattern"></div>
    <div class="ring"><svg width="76" height="76" viewBox="0 0 76 76" fill="none" stroke="#222" stroke-width="2.5"><path d="M64 30 A28 28 0 1 0 38 66"/><path d="M38 16 V38 L26 30"/><text x="40" y="70" font-size="32" fill="#222" stroke="none" font-family="Lato,sans-serif">24</text></svg></div></div>
  <h3 class="head-font">Information<br>Technology (IT)</h3><span class="down"></span>
</div>
<div class="abs service" style="left:450px;top:1917px">
  <div class="ring-wrap"><div class="bg" role="img" aria-label="Faint crossing line pattern"></div>
    <div class="ring"><svg width="76" height="76" viewBox="0 0 76 76" fill="none" stroke="#222" stroke-width="2.5"><circle cx="20" cy="38" r="6"/><circle cx="56" cy="38" r="6"/><rect x="13" y="46" width="14" height="18" rx="4"/><rect x="49" y="46" width="14" height="18" rx="4"/><path d="M12 20 H28 L32 10 L38 28 L42 16 H64"/></svg></div></div>
  <h3 class="head-font">Telecommunications</h3><span class="down"></span>
</div>
<div class="abs service" style="left:784px;top:1917px">
  <div class="ring-wrap"><div class="bg" role="img" aria-label="Faint crossing line pattern"></div>
    <div class="ring"><svg width="76" height="76" viewBox="0 0 76 76" fill="none" stroke="#222" stroke-width="2.5"><rect x="10" y="10" width="30" height="40" rx="3"/><path d="M15 18 H35 M15 28 H35 M15 38 H35"/><rect x="30" y="22" width="30" height="44" rx="2"/><circle cx="44" cy="52" r="8"/><path d="M50 34 H56 M50 40 H56 M58 60 L70 44"/></svg></div></div>
  <h3 class="head-font">Accounting &amp;<br>Finance</h3><span class="down"></span>
</div>

<!-- contact -->
<div class="abs band" style="top:2330px;height:550px"></div>
<svg class="abs" style="left:0;top:2265px" width="1200" height="90" viewBox="0 0 1200 90">
  <path d="M0 45 C200 0 450 10 600 15 C800 10 1000 0 1200 30 L1200 90 L0 90Z" fill="#f3f3f5"/>
  <path d="M30 45 C150 20 300 20 530 52 C380 80 200 90 30 45Z" fill="#e4e7eb"/>
  <path d="M90 60 C200 45 320 45 430 70 C320 90 180 88 90 60Z" fill="#cfd5dc"/>
  <path d="M1065 45 C1120 30 1170 25 1200 25 L1200 80 C1150 70 1100 60 1065 45Z" fill="#dfe3e8"/>
</svg>
<h2 class="abs section-title head-font" style="top:2392px">CONTACT <span class="red">FORM</span></h2>
<div class="abs input" style="left:214px;top:2477px;width:375px">First Name</div>
<div class="abs input" style="left:610px;top:2477px;width:376px">Last Name</div>
<div class="abs input" style="left:214px;top:2546px;width:375px">Email Address</div>
<div class="abs input" style="left:610px;top:2546px;width:376px">Phone</div>
<div class="abs input msg" style="left:214px;top:2615px;width:772px">Message</div>
<div class="pill red-bg" style="left:457px;top:2734px;width:251px;height:54px;border-radius:27px">SUBMIT MESSAGE <span class="arrow-dot"></span></div>

<!-- footer -->
<footer class="abs footer">
  <span class="social" style="left:527px"></span>
  <span class="social" style="left:579px"></span>
  <span class="social" style="left:631px"></span>
  <p class="info">Address : 234, Talvoro Network lorem ipsum &nbsp;| &nbsp;Phone : +1-404-555-0182 &nbsp;| &nbsp;Email : info@talvoro.net</p>
  <p class="copy">© 2019 Talvoro Network.All right reserved &nbsp;| &nbsp;Term of Use &nbsp;| &nbsp;Privacy Policy</p>
</footer>

</body>
</html>
```